Expedition Cruise Sales Website for the Polar Regions (Antarctica & Arctic)

This will be a website for selling cruises.
This site should have a homepage, a ship page, destinations, and itineraries.
I have created a file specifying each page, and it is attached.
Pages:
1. Home
2. Cruise Lines
- 2.1 Ships
3. Destinations
- 3.1 Region - 3.2 Country - 3.3 City
4. Itineraries
- 4.1 Itinerary
5. Blog / Travel Tips 6. About Us
7. Contact
Please take a look on the attached pdf
Target Market(s)
Expedition Travelers
Coding
Coded - Design and coding required
Number of Pages Required
5+ page
Font styles to use
Look and feel
Each slider illustrates characteristics of the customer's brand and the style your logo design should communicate.

```html
<!DOCTYPE html>
<html lang="en">
<head>
<meta charset="UTF-8">
<title>Privacy Policy – Polarvia</title>
<link href="https://fonts.googleapis.com/css2?family=Figtree:wght@400;500;600;700&display=swap" rel="stylesheet">
<style>
:root{
  --navy:#0f1c3d;
  --ink:#18233f;
  --text:#3d4452;
  --blue:#3578bb;
  --nav-blue:#4a86c9;
  --rule:#dcdfe4;
  --white:#ffffff;
}
*{box-sizing:border-box;margin:0;padding:0}
html,body{width:1200px;height:2677px;overflow:hidden}
body{position:relative;font-family:'Figtree',sans-serif;background:var(--white);color:var(--text)}
.hero{position:absolute;left:0;top:0;width:1200px;height:312px;
  background:linear-gradient(90deg,#2d4a35 0%,#4e6148 25%,#7e8a86 42%,#3d7f95 60%,#2a6d8a 80%,#1f5d7c 100%)}
.hero::after{content:"";position:absolute;inset:0;background:linear-gradient(180deg,rgba(15,28,61,.75) 0%,rgba(15,28,61,.35) 40%,rgba(15,28,61,.35) 100%)}
.nav{position:absolute;top:0;left:0;width:1200px;height:100px;z-index:2}
.brand{position:absolute;left:66px;top:31px;color:var(--white);font-weight:600;font-size:27px;line-height:36px}
.menu{position:absolute;left:378px;top:44px;display:flex;font-size:10px;font-weight:500;color:var(--white)}
.menu .active{color:var(--nav-blue)}
.phone{position:absolute;left:905px;top:42px;color:var(--white);font-size:12px;font-weight:500;display:flex;align-items:center;gap:5px}
.book{position:absolute;left:1025px;top:33px;width:100px;height:31px;background:var(--blue);color:var(--white);font-size:10px;font-weight:600;display:flex;align-items:center;justify-content:center}
.hero-title{position:absolute;top:132px;width:1200px;text-align:center;color:var(--white);font-size:40px;font-weight:600;z-index:2}
.crumbs{position:absolute;top:192px;width:1200px;text-align:center;color:var(--white);font-size:11px;z-index:2}
.crumbs b{font-weight:600;margin-left:10px}
.crumbs .sep{margin-left:12px}
.policy{position:absolute;left:200px;top:360px;width:800px}
.policy h1{font-size:22px;font-weight:600;color:var(--ink);margin-bottom:22px}
.policy .lead{font-size:12.3px;line-height:22.6px;color:var(--text);padding-bottom:30px;border-bottom:1px solid var(--rule)}
.clause{border-bottom:1px solid var(--rule);height:179px;padding-top:30px}
.clause:last-child{border-bottom:none}
.clause h2{font-size:19.5px;font-weight:600;color:var(--ink);margin-bottom:17px}
.clause p{font-size:9.6px;line-height:18.8px;color:var(--ink)}
.newsletter{position:absolute;left:0;top:1902px;width:1200px;height:425px;background:var(--blue)}
.news-copy{position:absolute;left:106px;top:1990px;color:var(--white)}
.news-copy h3{font-size:30px;font-weight:400;line-height:35px}
.news-copy h3 strong{font-weight:700}
.news-copy p{font-size:12.4px;line-height:14.5px;margin-top:19px}
.form{position:absolute;left:106px;top:2128px;width:482px;display:grid;grid-template-columns:235px 235px;gap:12px}
.field{height:31px;background:var(--white);font-size:9px;color:var(--ink);padding-left:14px;display:flex;align-items:center}
.submit{position:absolute;left:106px;top:2216px;width:100px;height:31px;background:var(--navy);color:var(--white);font-size:10px;font-weight:600;display:flex;align-items:center;justify-content:center}
.ship-photo{position:absolute;left:706px;top:1845px;width:388px;height:480px;
  background:linear-gradient(180deg,#dcdee2 0%,#c9ccd2 45%,#4b515c 62%,#9da6b0 75%,#e7eaee 100%)}
.footer{position:absolute;left:0;top:2327px;width:1200px;height:350px;background:linear-gradient(180deg,#26355c 0%,#1f2d52 60%,#1a2747 100%);color:var(--white)}
.f-brand{position:absolute;left:106px;top:92px;font-size:27px;font-weight:600;line-height:36px}
.f-about{position:absolute;left:106px;top:140px;width:400px;font-size:9.6px;line-height:18.8px}
.f-col h4{font-size:13px;font-weight:600;margin-bottom:14px}
.f-contact{position:absolute;left:587px;top:82px;font-size:10.5px}
.f-contact .row{display:flex;align-items:center;gap:9px;margin-bottom:12px}
.f-contact .row.small{font-size:9px}
.f-follow{position:absolute;left:587px;top:170px}
.socials{display:flex;gap:6px}
.socials span{width:32px;height:32px;border:1px solid rgba(255,255,255,.8);border-radius:50%}
.f-links{position:absolute;left:819px;top:82px}
.links{display:grid;grid-template-columns:105px 110px;grid-auto-flow:column;grid-template-rows:repeat(7,18.8px);font-size:9.4px}
.f-rule{position:absolute;left:106px;top:278px;width:988px;height:1px;background:rgba(255,255,255,.2)}
.copyright{position:absolute;left:106px;top:311px;font-size:9.5px}
.copyright b{font-weight:600}
.to-top{position:absolute;left:1130px;top:2596px}
.chat{position:absolute;left:1057px;top:2301px;width:112px;height:48px;background:var(--white);border-radius:3px;box-shadow:0 2px 8px rgba(0,0,0,.15);color:var(--ink);padding:8px 9px;font-size:7px}
.chat .big{font-size:13px;font-weight:700;color:var(--blue)}
.chat .dot{position:absolute;right:10px;top:-18px;width:36px;height:36px;border-radius:50%;background:var(--blue);border:2px solid var(--white)}
</style>
</head>
<body>
<header class="hero" role="img" aria-label="Photo of a rocky tropical coastline with a beach and swimmers"></header>
<nav class="nav">
  <div class="brand">Polarvia</div>
  <div class="menu">
    <span class="active" style="width:64px">Home</span>
    <span style="width:88px">Cruise lines</span>
    <span style="width:92px">Destinations</span>
    <span style="width:81px">Itineraries</span>
    <span style="width:60px">Blog</span>
    <span style="width:77px">About us</span>
    <span>Contact</span>
  </div>
  <div class="phone"><svg width="10" height="10" viewBox="0 0 24 24" fill="none" stroke="#fff" stroke-width="2.4"><path d="M5 3h4l2 5-3 2a12 12 0 0 0 6 6l2-3 5 2v4a2 2 0 0 1-2 2A18 18 0 0 1 3 5a2 2 0 0 1 2-2z"/></svg>555.010.2040</div>
  <div class="book">Book Now!</div>
</nav>
<h1 class="hero-title">Privacy Policy</h1>
<div class="crumbs">Home <span class="sep">&gt;&gt;</span> <b>Privacy Policy</b></div>

<main class="policy">
  <h1>Privacy Policy &amp; Terms of use</h1>
  <p class="lead">It is a long established fact that a reader will be distracted by the readable content of a page when looking at its layout. the point of<br>using lorem ipsum is that it has a more-or-less normal distribution of letters, as opposed to using 'content here, content here', making it look like<br>readable english. many desktop publishing packages and web page editors now use lorem ipsum as their default model text, and a search for<br>'lorem ipsum' will uncover many web sites still in their infancy. various versions have evolved over the years,<br>sometimes by accident, sometimes on purpose (injected humour and the like).</p>
  <section class="clause"><h2>Contrary to popular belief</h2><p>It is a long established fact that a reader will be distracted by the readable content of a page when looking at its layout. The point of using lorem ipsum is that it has a<br>more-or-less normal distribution of letters, as opposed to using 'content here, content here', making it look like readable english. many desktop publishing packages and web<br>page editors now use lorem ipsum as their default model text, and a search for 'lorem ipsum' will uncover many web sites still in their infancy. various versions<br>have evolved over the years, sometimes by accident, sometimes on purpose (injected humour and the like).</p></section>
  <section class="clause"><h2>It is a long established fact</h2><p>It is a long established fact that a reader will be distracted by the readable content of a page when looking at its layout. The point of using lorem ipsum is that it has a<br>more-or-less normal distribution of letters, as opposed to using 'content here, content here', making it look like readable english. many desktop publishing packages and web<br>page editors now use lorem ipsum as their default model text, and a search for 'lorem ipsum' will uncover many web sites still in their infancy. various versions<br>have evolved over the years, sometimes by accident, sometimes on purpose (injected humour and the like).</p></section>
  <section class="clause"><h2>But i must explain to you how</h2><p>It is a long established fact that a reader will be distracted by the readable content of a page when looking at its layout. The point of using lorem ipsum is that it has a<br>more-or-less normal distribution of letters, as opposed to using 'content here, content here', making it look like readable english. many desktop publishing packages and web<br>page editors now use lorem ipsum as their default model text, and a search for 'lorem ipsum' will uncover many web sites still in their infancy. various versions<br>have evolved over the years, sometimes by accident, sometimes on purpose (injected humour and the like).</p></section>
  <section class="clause"><h2>At vero eos et accusamus et iusto</h2><p>It is a long established fact that a reader will be distracted by the readable content of a page when looking at its layout. The point of using lorem ipsum is that it has a<br>more-or-less normal distribution of letters, as opposed to using 'content here, content here', making it look like readable english. many desktop publishing packages and web<br>page editors now use lorem ipsum as their default model text, and a search for 'lorem ipsum' will uncover many web sites still in their infancy. various versions<br>have evolved over the years, sometimes by accident, sometimes on purpose (injected humour and the like).</p></section>
  <section class="clause"><h2>On the other hand, we denounce</h2><p>It is a long established fact that a reader will be distracted by the readable content of a page when looking at its layout. The point of using lorem ipsum is that it has a<br>more-or-less normal distribution of letters, as opposed to using 'content here, content here', making it look like readable english. many desktop publishing packages and web<br>page editors now use lorem ipsum as their default model text, and a search for 'lorem ipsum' will uncover many web sites still in their infancy. various versions<br>have evolved over the years, sometimes by accident, sometimes on purpose (injected humour and the like).</p></section>
  <section class="clause"><h2>Mistaken idea of denouncing pleasure</h2><p>It is a long established fact that a reader will be distracted by the readable content of a page when looking at its layout. The point of using lorem ipsum is that it has a<br>more-or-less normal distribution of letters, as opposed to using 'content here, content here', making it look like readable english. many desktop publishing packages and web<br>page editors now use lorem ipsum as their default model text, and a search for 'lorem ipsum' will uncover many web sites still in their infancy. various versions<br>have evolved over the years, sometimes by accident, sometimes on purpose (injected humour and the like).</p></section>
  <section class="clause"><h2>Nam libero tempore, cum soluta</h2><p>It is a long established fact that a reader will be distracted by the readable content of a page when looking at its layout. The point of using lorem ipsum is that it has a<br>more-or-less normal distribution of letters, as opposed to using 'content here, content here', making it look like readable english. many desktop publishing packages and web<br>page editors now use lorem ipsum as their default model text, and a search for 'lorem ipsum' will uncover many web sites still in their infancy. various versions<br>have evolved over the years, sometimes by accident, sometimes on purpose (injected humour and the like).</p></section>
</main>

<section class="newsletter"></section>
<div class="news-copy">
  <h3>Get cruise deals <strong>directly</strong><br><strong>in your inbox</strong></h3>
  <p>Subscribe now and set sail on a journey of endless adventure with<br>our exclusive cruise newsletter</p>
</div>
<div class="form">
  <div class="field">First Name</div><div class="field">Last Name</div>
  <div class="field">Email Address...</div><div class="field">Mobile Number</div>
</div>
<div class="submit">Submit</div>
<div class="ship-photo" role="img" aria-label="Photo of an expedition cruise ship among sea ice in polar waters"></div>

<footer class="footer" role="contentinfo">
  <div class="f-brand">Polarvia</div>
  <p class="f-about">Lorem Ipsum is simply dummy text of the printing and typesetting industry.<br>Lorem Ipsum has been the industry's standard dummy text ever since the 1500s,<br>when an unknown printer took a galley of type and scrambled it to<br>make a type specimen book.</p>
  <div class="f-col f-contact">
    <h4>Contct Us</h4>
    <div class="row"><svg width="10" height="10" viewBox="0 0 24 24" fill="none" stroke="#fff" stroke-width="2.4"><path d="M5 3h4l2 5-3 2a12 12 0 0 0 6 6l2-3 5 2v4a2 2 0 0 1-2 2A18 18 0 0 1 3 5a2 2 0 0 1 2-2z"/></svg>555.010.2040</div>
    <div class="row small"><svg width="10" height="9" viewBox="0 0 24 20" fill="#fff"><path d="M2 6l10 6 10-6v12H2z M2 3h20v2L12 11 2 5z"/></svg>hello@polarviatrips.com</div>
  </div>
  <div class="f-col f-follow">
    <h4>Follow us</h4>
    <div class="socials"><span aria-label="Social profile"></span><span aria-label="Social profile"></span><span aria-label="Social profile"></span><span aria-label="Social profile"></span></div>
  </div>
  <div class="f-col f-links">
    <h4>Quick Links</h4>
    <div class="links">
      <span>Home</span><span>Cruise Lines</span><span>Destinations</span><span>Itineraries</span><span>Blog</span><span>About Us</span><span>Contact</span>
      <span>FAQ</span><span>Privacy Policy</span><span>Terms and Conditions</span><span>Booking Confirmation</span>
    </div>
  </div>
  <div class="f-rule"></div>
  <p class="copyright">© 2025 <b>Polarvia</b> All Rights Reserved</p>
</footer>
<svg class="to-top" width="16" height="18" viewBox="0 0 16 18" aria-label="Back to top"><path d="M8 0L16 18 8 13 0 18z" fill="#fff"/></svg>
<div class="chat"><span class="dot"></span>Available<br><span class="big">24/7</span> to Assist with<br>Any Questions</div>
</body>
</html>
```